KR Appraisals website redesign

I would like to refresh my existing website of www.krappraisals-example.com with new graphics, look and feel, as well as updated structure and wording. Content and layout changes have been uploaded to this project Brief.

My existing website has a dark feel. I am now looking for a light and energetic feel. Financial Services is my industry, so the website should be reflect that. I would also like to reflect the concepts of Trust, Service and Expertise.

The website must be serious and upmarket.

Target Market(s)

Corporate board members, CFO's, treasurers and controllers
Auditors, tax advisors, private equity and venture capital asset managers, investors, tax authorities

Industry/Entity Type

Financial Service

Coding

Coded - Design and coding required

Number of Pages Required

5+ page

Font styles to use
Sans Serif
Other font styles liked:
• Designer can choose another modern font

Colors
0355a3
3277b5
85acd3
eaf1f7
f37122
f68d4d
9bcb3c
acd037
cadf82

Requirements
Must have
• Good hi resolution pictures that convey "Finance", "Trust", "Service" or "Expertise".
• An anti-bot (such as Captcha) mechanism in the contact form.
Should not have
• Must not have all content on one rolling screen.

```html
<!DOCTYPE html>
<html lang="en">
<head>
<meta charset="utf-8">
<title>KR Appraisals</title>
<link href="https://fonts.googleapis.com/css2?family=Open+Sans:wght@400;600;700&display=swap" rel="stylesheet">
<style>
:root{
  --navy:#0b1424;
  --navy-2:#1b2a44;
  --blue:#0355a3;
  --blue-mid:#3277b5;
  --blue-soft:#85acd3;
  --blue-pale:#eaf1f7;
  --orange:#f37122;
  --green:#9bcb3c;
  --ink:#1d1d1d;
  --body:#5b5b5b;
  --line:#e3e3e3;
  --card:#f6f6f6;
  --white:#ffffff;
}
*{box-sizing:border-box;margin:0;padding:0}
html,body{width:1200px;height:4085px;overflow:hidden}
body{position:relative;background:var(--white);font-family:"Open Sans",Arial,sans-serif;color:var(--body)}
.abs{position:absolute}

/* hero */
.hero-photo{left:0;top:0;width:1200px;height:640px;
  background:linear-gradient(160deg,#2f3e58 0%,#1e2b42 40%,#121c2e 100%);
  clip-path:polygon(0 0,1200px 0,1200px 547px,600px 637px,0 547px)}
.brand{left:95px;top:30px;color:var(--white);font-weight:600;font-size:20px;letter-spacing:1px;display:flex;align-items:center;gap:8px}
.brand-square{width:14px;height:14px;border:2px solid var(--white)}
.nav{right:94px;top:41px;display:flex;gap:0}
.nav a{color:var(--white);text-decoration:none;font-size:12.5px;margin-left:33px}
.hero-mark{left:554px;top:211px;width:92px;height:92px;border-radius:50%;background:var(--blue);color:var(--white);font-weight:600;font-size:28px;display:flex;align-items:center;justify-content:center}
.hero-title{left:0;top:306px;width:1200px;text-align:center;color:var(--white);font-size:40px;line-height:48px;font-weight:400}
.slide-nav{left:1074px;top:172px;width:24px;color:#b9c2d0;font-size:11px;text-align:center;line-height:19px}
.slide-nav .rule{width:24px;border-top:1px solid #b9c2d0;margin:4px 0}

/* guide lines */
.guides{left:0;top:0;width:1200px;height:4085px;pointer-events:none}
.rule-h{height:1px;background:var(--line);left:95px;width:1011px}

/* values */
.value{top:819px;width:322px;height:313px;background:var(--card);border:1px solid var(--line);text-align:center;padding:50px 34px 0}
.value.is-active{background:var(--blue);border-color:var(--blue)}
.value svg{display:block;margin:0 auto;height:76px}
.value h3{font-size:19px;font-weight:600;letter-spacing:1px;margin-top:12px}
.value p{font-size:12.5px;line-height:19.5px;margin-top:15px}
.value.is-active h3,.value.is-active p{color:var(--white)}
.value.service h3{color:var(--orange)}
.value.expertise h3{color:var(--green)}

/* services */
.service-photo{width:424px;height:353px}
.service-text{width:380px}
.service-text h2{font-size:19.5px;font-weight:600;color:var(--ink);letter-spacing:.3px}
.service-text p{font-size:12.3px;line-height:19.4px;margin-top:17px;color:var(--body)}

/* footer */
.footer{left:0;top:3181px;width:1200px;height:904px;background:var(--navy);
  clip-path:polygon(600px 0,1200px 89px,1200px 904px,0 904px,0 89px)}
.foot-brand{left:0;top:3282px;width:1200px;text-align:center;color:var(--white);font-size:30px;font-weight:600;letter-spacing:2px}
.foot-rule{left:95px;width:1011px;height:1px;background:#24304a}
.contact-title{left:0;top:3396px;width:1200px;text-align:center;color:var(--white);font-size:33px;font-weight:700;letter-spacing:1.5px}
.contact-intro{left:0;top:3444px;width:1200px;text-align:center;color:#a9b2c2;font-size:11px;line-height:18px}
.field{border:1px solid #3a4660;background:transparent;color:#8c96a8;font-size:11px;padding:14px 16px}
.captcha{left:420px;top:3704px;width:217px;height:51px;background:#f9f9f9;border:1px solid #d3d3d3;display:flex;align-items:center;padding-left:10px;font-size:11px;color:#222}
.captcha .box{width:20px;height:20px;border:2px solid #c1c1c1;border-radius:2px;background:#fff;margin-right:12px}
.captcha .seal{position:absolute;right:10px;top:12px;width:26px;height:26px;background:var(--blue-soft);border-radius:4px}
.send{left:651px;top:3712px;width:122px;height:37px;background:var(--blue);color:var(--white);font-size:12px;font-weight:700;display:flex;align-items:center;justify-content:center}
.address{left:0;top:3829px;width:1200px;text-align:center;color:var(--white);font-size:17px;line-height:28px}
.badge{top:3910px;height:38px;background:#3a4660;border-radius:19px}
.copyright{left:0;top:4007px;width:1200px;text-align:center;color:var(--blue-mid);font-size:13px}
</style>
</head>
<body>

<!-- hero -->
<div class="abs hero-photo" role="img" aria-label="Overhead photo of business people meeting around a desk with a laptop, in deep navy tones"></div>
<div class="abs brand"><span class="brand-square"></span>KR APPRAISALS</div>
<nav class="abs nav"><a>Home</a><a>About</a><a>Services</a><a>News &amp; Views</a><a>Contact</a></nav>
<div class="abs hero-mark">KR</div>
<h1 class="abs hero-title">Expertise is core to the<br>philosophy of KR Appraisals.</h1>
<div class="abs slide-nav">↑<br>N<br>E<br>X<br>T<div class="rule"></div>P<br>R<br>E<br>V<br>↓</div>

<!-- guide lines -->
<svg class="abs guides" width="1200" height="4085" viewBox="0 0 1200 4085">
  <polyline points="0,599 600,691 1200,599" fill="none" stroke="#ececec" stroke-width="1"/>
  <line x1="600" y1="691" x2="600" y2="777" stroke="#ececec"/>
  <line x1="600" y1="1183" x2="600" y2="3130" stroke="#ececec"/>
  <polyline points="0,3220 600,3130 1200,3220" fill="none" stroke="#ececec" stroke-width="1"/>
</svg>
<div class="abs rule-h" style="top:777px"></div>
<div class="abs rule-h" style="top:785px"></div>

<!-- values -->
<section class="abs value is-active" style="left:95px">
  <svg viewBox="0 0 100 60" width="100" fill="none" stroke="#fff" stroke-width="2.5" stroke-linejoin="round" stroke-linecap="round">
    <path d="M4 10h14v34H4M96 10H82v34h14"/>
    <path d="M18 16h14l14 6 10-6h26M18 40l12 10c3 2 6 2 8 0l20-14M82 40l-10 6"/>
    <path d="M46 22l-8 8c-2 2 0 5 3 4l12-6 20 14"/>
  </svg>
  <h3>TRUST</h3>
  <p>Trust is paramount. Clients rely on KR Appraisals for confidentiality, transparency and independence.</p>
</section>
<section class="abs value service" style="left:441px">
  <svg viewBox="0 0 80 70" width="80" fill="none" stroke="#f37122" stroke-width="2.5">
    <circle cx="22" cy="16" r="10"/><path d="M6 44c0-10 7-16 16-16s16 6 16 16z"/>
    <circle cx="52" cy="30" r="10"/><path d="M36 66c0-12 7-18 16-18s16 6 16 18z"/>
    <rect x="4" y="50" width="24" height="16"/>
  </svg>
  <h3>SERVICE</h3>
  <p>Service is front and center at KR Appraisals. We consider the needs of all stakeholders and the personal needs of the client team involved.</p>
</section>
<section class="abs value expertise" style="left:786px">
  <svg viewBox="0 0 60 80" width="60" fill="none" stroke="#9bcb3c" stroke-width="2.5">
    <circle cx="30" cy="22" r="14"/><path d="M16 18h28"/>
    <path d="M6 78V56c0-10 10-16 24-16s24 6 24 16v22z"/><path d="M30 42v36M20 60h8"/>
  </svg>
  <h3>EXPERTISE</h3>
  <p>Expertise is core to the philosophy of KR Appraisals. Our global network of professionals maintain and continue to develop the knowledge and experience that you expect from your trusted corporate finance partner.</p>
</section>
<div class="abs rule-h" style="top:1175px"></div>
<div class="abs rule-h" style="top:1183px"></div>

<!-- services -->
<div class="abs service-photo" style="left:176px;top:1266px;background:linear-gradient(135deg,#f2c28a 0%,#c9a27a 35%,#6b6058 70%,#e8e6e2 100%)" role="img" aria-label="Photo of a hand pointing at financial charts on a desk in warm sunlight"></div>
<article class="abs service-text" style="left:643px;top:1372px">
  <h2>Business Valuation</h2>
  <p>Company stakeholders trust KR Appraisals to provide business valuations for transaction, accounting, tax, legal, and share or option participation purposes. Through our bespoke approach and global network, we customize teams to the needs of our clients.</p>
</article>

<article class="abs service-text" style="left:174px;top:1724px">
  <h2>Intellectual Property Valuation</h2>
  <p>Patents, unpatented technologies, know how, brands, trademarks, databases, customer-related assets - this is a limited sample of the wide universe of intellectual property that clients trust KR Appraisals to value. There are many techniques for valuing intellectual property and no two assets are alike. Trust KR Appraisals for our expertise and client-centric approach.</p>
</article>
<div class="abs service-photo" style="left:600px;top:1619px;background:linear-gradient(135deg,#c9c4bd 0%,#8a7868 40%,#3a3633 75%,#1f2530 100%)" role="img" aria-label="Photo of a small house model being handed across a table"></div>

<div class="abs service-photo" style="left:176px;top:1973px;background:linear-gradient(135deg,#5a3f2c 0%,#8a6a50 40%,#d9d9dc 65%,#6b4a34 100%)" role="img" aria-label="Photo of people reviewing printed charts beside a laptop on a wooden table"></div>
<article class="abs service-text" style="left:645px;top:2079px">
  <h2>M&amp;A Advisory</h2>
  <p>Through our international network of M&amp;A professionals, KR Appraisals can assist companies with buying other companies or selling (parts of) their companies. KR Appraisals offers a flexible approach, assisting companies with part of the process or providing a full-service approach.</p>
</article>

<article class="abs service-text" style="left:176px;top:2431px">
  <h2>Business Plan Coaching</h2>
  <p>Young companies and entrepreneurs frequently ask for our advice on their business plans and strategies. With almost 2 decades of analyzing companies large and small, we are well positioned to advise companies based on experience and insight.</p>
</article>
<div class="abs service-photo" style="left:600px;top:2326px;background:linear-gradient(135deg,#e9e9ea 0%,#cfd2d6 40%,#4a4b50 75%,#1e1f24 100%)" role="img" aria-label="Photo of a presenter at a whiteboard with a team in a bright office"></div>

<div class="abs service-photo" style="left:176px;top:2680px;background:linear-gradient(135deg,#dcd6d0 0%,#8a8079 40%,#3c3a3b 75%,#2a2a2c 100%)" role="img" aria-label="Photo of hands holding a payment card and a smartphone"></div>
<article class="abs service-text" style="left:645px;top:2749px">
  <h2>Purchase Price Allocation</h2>
  <p>Accounting procedures require an acquiror to allocate purchase consideration to the fair value of all acquired assets and liabilities when obtaining control of a company. This process, called a purchase price allocation (PPA), involves assets and liabilities that did not exist on the target's balance sheet prior to the transaction. Certain pre-existing assets must be restated to fair value. This process can be time consuming and complex. KR Appraisals has a wealth of experience in this area and can work with you and your independent auditor to achieve a smooth process.</p>
</article>

<!-- footer -->
<footer class="abs footer"></footer>
<div class="abs foot-brand">KR APPRAISALS</div>
<div class="abs foot-rule" style="top:3363px"></div>
<h2 class="abs contact-title">GET IN TOUCH</h2>
<p class="abs contact-intro">Please do not hesitate to contact us by phone, email, post or by completing form on the right hand side of this page.<br>We look forward to hearing from you.</p>
<div class="abs field" style="left:254px;top:3493px;width:340px;height:43px">Enter Your Namre</div>
<div class="abs field" style="left:605px;top:3493px;width:341px;height:43px">Enter Your Email</div>
<div class="abs field" style="left:254px;top:3546px;width:340px;height:43px">Company Name</div>
<div class="abs field" style="left:605px;top:3546px;width:341px;height:43px">Phone No.</div>
<div class="abs field" style="left:254px;top:3598px;width:692px;height:94px">Comments</div>
<div class="abs captcha"><span class="box"></span>I'm not a robot<span class="seal"></span></div>
<div class="abs send">Send Message</div>
<div class="abs foot-rule" style="top:3801px"></div>
<address class="abs address" style="font-style:normal">Location:&nbsp; Keizerstraat 48&nbsp; 1016 DL Amsterdam&nbsp; The Netherlands<br>Telephone Number: +31 20 555 0148</address>
<div class="abs badge" style="left:444px;width:119px"></div>
<div class="abs badge" style="left:586px;width:172px"></div>
<div class="abs foot-rule" style="top:3988px"></div>
<p class="abs copyright">© Copyright KR Appraisals 2019 All Rights Reserved</p>

</body>
</html>
```